website design Investment Fund

I am looking for a custom website that will work on desktop computer, tablet device and a cellular device. I have attached the booklet so you can get an idea of the look we are going for. Would like to use the website eventually for crowdfunding. We like the ski racer and mountain climbing designs.

Target Market(s)

Financial Services

Industry/Entity Type

Financial Service

Coding

Coded - Design and coding required

Number of Pages Required

5+ page

Font styles to use
Sans Serif

Requirements
Must have
• Must be viewable on a cell phone and tablet and desktop
Nice to have
• Contact us form

```html
<!DOCTYPE html>
<html lang="en">
<head>
<meta charset="utf-8">
<title>Vantor Capital II – Secured Income Fund</title>
<link rel="stylesheet" href="https://fonts.googleapis.com/css2?family=Lato:wght@400;700;900&display=swap">
<style>
:root{
  --red:#e1091f;
  --blue:#1c3f94;
  --navy:#14306f;
  --ink:#333;
  --dark:#2c2c2e;
  --grey:#f3f3f3;
  --muted:#555;
}
*{box-sizing:border-box;margin:0;padding:0}
html,body{width:1200px;height:4183px;overflow:hidden;background:#fff}
body{font-family:'Lato',sans-serif;color:var(--ink)}
.page{position:relative;width:1200px;height:4183px;overflow:hidden}
.abs{position:absolute}
.btn{position:absolute;display:flex;align-items:center;justify-content:center;color:#fff;font-weight:700;font-size:17px;text-transform:uppercase;background:linear-gradient(90deg,var(--red) 20%,var(--blue) 100%)}
.section-title{position:absolute;left:0;width:1200px;text-align:center;font-weight:900;font-size:35px;color:var(--ink);text-transform:uppercase}

.topbar{left:0;top:0;width:1200px;height:58px;background:var(--dark);color:#fff;font-size:16px;font-weight:700}
.topbar .contact{position:absolute;right:75px;top:19px;display:flex;gap:16px;align-items:center}
.topbar svg{vertical-align:-2px;margin-right:10px}
.header{left:0;top:58px;width:1200px;height:114px;background:#fff}
.brand{position:absolute;left:73px;top:60px;font-weight:900;font-size:22px;color:var(--ink);display:flex;align-items:center;gap:10px}
.brand .mark{width:16px;height:16px;background:var(--red)}
.brand small{display:block;font-size:12px;font-weight:700;letter-spacing:.5px;text-align:center}
.nav{position:absolute;right:75px;top:50px;display:flex;gap:35px;font-size:15px;font-weight:700}
.nav a{color:var(--ink);text-decoration:none}
.nav a.active{color:var(--red)}

.hero{left:0;top:172px;width:1200px;height:778px}
.hero h1{position:absolute;left:75px;top:165px;color:#fff;font-size:62px;font-weight:900;line-height:1}
.hero h2{position:absolute;left:75px;top:232px;color:#fff;font-size:32px;font-weight:900}
.quick{position:absolute;left:794px;top:107px;width:331px;height:423px;background:#fff;box-shadow:0 2px 10px rgba(0,0,0,.2)}
.quick h3{height:48px;background:#1b1b1b;color:#fff;font-size:27px;font-weight:900;text-align:center;line-height:52px}
.quick .field{position:absolute;left:22px;width:290px;height:42px;border:1px solid #ccc;font-size:14px;font-weight:700;padding:12px 12px;color:#222}
.quick .btn{left:22px;width:290px;height:42px;font-size:17px}

.about-text{position:absolute;top:1050px;width:430px;font-size:14.5px;line-height:26px;color:var(--muted)}

.services{left:0;top:1470px;width:1200px;height:544px;background:linear-gradient(180deg,#fff 0%,#fff 55%,#c9cdd2 78%,#6f7479 100%)}
.service{position:absolute;top:0;width:480px;text-align:center}
.service .icon{margin:85px auto 0;width:88px;height:88px;border:2px solid var(--red);border-radius:50%;display:flex;align-items:center;justify-content:center}
.service h4{margin-top:28px;color:var(--red);font-size:22px;font-weight:900;line-height:28px;text-transform:uppercase}
.service p{margin-top:12px;font-size:15px;line-height:26px;color:var(--muted)}

.team{left:0;top:2014px;width:1200px;height:479px}
.member{position:absolute;top:131px;width:242px;text-align:center}
.member .photo{width:242px;height:207px;border:3px solid #ccc;background:linear-gradient(180deg,#eef0f2,#b9bcc1)}
.member h5{margin-top:35px;font-size:20px;font-weight:900;color:var(--blue)}
.member span{display:block;margin-top:5px;font-size:14px;font-weight:700;color:var(--red)}

.banner{left:0;top:2493px;width:1200px;height:369px;background:linear-gradient(135deg,#233d7a,#0f2a66 60%,#162f6b)}
.banner p{position:absolute;left:0;top:100px;width:1200px;text-align:center;color:#fff;font-weight:900;font-size:30px;line-height:37px;text-transform:uppercase;text-shadow:0 2px 4px rgba(0,0,0,.4)}

.post{position:absolute;top:2985px;width:512px}
.post .img{height:263px}
.post h6{margin-top:48px;font-size:20px;font-weight:900;color:var(--blue);text-transform:uppercase}
.post p{margin-top:8px;font-size:14.5px;line-height:27px;color:var(--muted)}
.post .btn{position:relative;margin-top:20px;width:150px;height:46px;font-size:15px}
.dots{position:absolute;left:564px;top:3522px;display:flex;gap:12px}
.dots i{width:14px;height:14px;border-radius:50%;background:var(--blue)}
.dots i:first-child{background:var(--red)}

.footer{left:0;top:3589px;width:1200px;height:594px}
.fcol{position:absolute;top:3960px;color:#fff}
.fcol h6{font-size:19px;font-weight:700;text-transform:uppercase;margin-bottom:14px}
.fcol a,.fcol li{display:block;color:#ccc;text-decoration:none;font-size:14px;line-height:32px;list-style:none}
.fbrand{position:absolute;left:75px;top:4045px;color:#fff;font-weight:900;font-size:18px}
.fbrand small{display:block;font-size:10px;font-weight:700;text-align:center}
.copy{position:absolute;left:75px;top:4100px;color:#ccc;font-size:12px;line-height:21px}
.info li{padding-left:33px;position:relative;line-height:21px;margin-bottom:8px}
.info svg{position:absolute;left:0;top:3px}
.email-box{width:257px;height:42px;background:#fff;font-size:14px;color:#333;padding:13px 12px}
.signup{position:absolute;left:1038px;top:4085px;width:88px;height:38px;background:var(--blue);color:#fff;font-size:14px;font-weight:700;display:flex;align-items:center;justify-content:center}
.social{position:absolute;left:872px;top:4138px;display:flex;gap:20px}
.social i{width:22px;height:22px;border-radius:50%;border:2px solid #bbb}
</style>
</head>
<body>
<div class="page">

  <div class="abs topbar">
    <div class="contact">
      <span><svg width="14" height="14" viewBox="0 0 24 24" fill="#fff"><path d="M6.6 10.8c1.4 2.8 3.8 5.1 6.6 6.6l2.2-2.2c.3-.3.7-.4 1-.2 1.1.4 2.3.6 3.6.6.6 0 1 .4 1 1V20c0 .6-.4 1-1 1C10.6 21 3 13.4 3 4c0-.6.4-1 1-1h3.5c.6 0 1 .4 1 1 0 1.3.2 2.5.6 3.6.1.3 0 .7-.2 1z"/></svg>1-800-555-0142</span>
      <span><svg width="16" height="13" viewBox="0 0 24 18" fill="#fff"><path d="M0 0h24v2L12 10 0 2z M0 4l12 8 12-8v14H0z"/></svg>info@vantorcapital.com</span>
    </div>
  </div>

  <div class="abs header">
    <div class="brand"><span class="mark"></span><span>VANTOR CAPITAL II<small>MANAGEMENT, LLC</small></span></div>
    <nav class="nav">
      <a class="active" href="#">HOME</a><a href="#">ABOUT US</a><a href="#">SERVICIES</a><a href="#">OUR TEAM</a><a href="#">BLOG</a><a href="#">CLIENTS</a><a href="#">CONTACT US</a>
    </nav>
  </div>

  <section class="abs hero">
    <svg width="1200" height="778" viewBox="0 0 1200 778" style="position:absolute;left:0;top:0">
      <defs>
        <linearGradient id="heroPhoto" x1="0" y1="0" x2="1" y2="1">
          <stop offset="0" stop-color="#cfcfcf"/><stop offset=".55" stop-color="#8a8a8a"/><stop offset="1" stop-color="#3a3a3a"/>
        </linearGradient>
      </defs>
      <polygon role="img" aria-label="Black and white photo of two mountain climbers facing a rocky peak" fill="url(#heroPhoto)" points="0,0 1200,0 1200,300 460,627 0,372"/>
      <polygon fill="var(--blue)" points="0,510 300,680 0,778"/>
      <polygon fill="var(--red)" points="0,372 460,627 1200,300 1200,470 780,590 419,748 0,510"/>
      <polygon fill="var(--blue)" points="780,590 1200,470 1200,778"/>
      <polygon fill="#fff" points="0,778 300,680 419,748 780,590 1200,778"/>
    </svg>
    <h1>VANTOR CAPITAL II</h1>
    <h2>SECURED INCOME FUND</h2>
    <form class="quick">
      <h3>QUICK CONTACT</h3>
      <div class="field" style="top:66px">Name</div>
      <div class="field" style="top:120px">Email Address</div>
      <div class="field" style="top:171px">Phone No</div>
      <div class="field" style="top:225px;">Subject</div>
      <div class="field" style="top:276px;height:76px">Message</div>
      <div class="btn" style="top:364px">SUBMIT NOW</div>
    </form>
  </section>

  <h2 class="section-title" style="top:985px">ABOUT OUR COMPANY</h2>
  <p class="about-text" style="left:164px">Vantor Capital is a privately held mortgage lender, asset management and advisory firm headquartered in Redmoor Bay, Westland which specializes in fast financing for debt, equity, mezzanine and land bank on real estate projects in the $100,000 to $50,000,000 range.</p>
  <p class="about-text" style="left:614px">As a highly reputable, successful and growth-focused company with decades of experience across the entire spectrum of real estate financing through Westland, the Southern Coast and the Islands. At Vantor Capital, we've created an exceptional business focused on delivering.</p>
  <div class="btn" style="left:510px;top:1221px;width:180px;height:49px">READ MORE</div>

  <svg class="abs" style="left:0;top:1270px" width="1200" height="200" viewBox="0 0 1200 200">
    <rect x="0" y="88" width="1200" height="112" fill="var(--grey)"/>
    <polygon fill="var(--red)" points="918,88 1200,0 1200,88"/>
  </svg>
  <h2 class="section-title" style="top:1395px">WHAT WE DO</h2>

  <section class="abs services">
    <svg width="1200" height="544" viewBox="0 0 1200 544" style="position:absolute;left:0;top:0">
      <defs><linearGradient id="mist" x1="0" y1="0" x2="0" y2="1"><stop offset="0" stop-color="#d7dadd" stop-opacity="0"/><stop offset="1" stop-color="#5d6368"/></linearGradient></defs>
      <polygon fill="var(--blue)" points="0,0 292,0 0,93"/>
      <rect role="img" aria-label="Misty mountain range under clouds" x="0" y="370" width="1200" height="174" fill="url(#mist)"/>
    </svg>
    <div class="service" style="left:91px">
      <div class="icon"><svg width="40" height="34" viewBox="0 0 40 34" fill="#444"><circle cx="20" cy="8" r="7"/><circle cx="8" cy="12" r="5"/><circle cx="32" cy="12" r="5"/><path d="M9 34c0-8 5-13 11-13s11 5 11 13z"/><path d="M0 30c0-6 3-10 8-10 2 0 3 .5 4 1-3 3-4 6-4 9z"/><path d="M40 30c0-6-3-10-8-10-2 0-3 .5-4 1 3 3 4 6 4 9z"/></svg></div>
      <h4>THE BOUTIQUE FUND<br>INVESTORS ARE LOOKING FOR</h4>
      <p>Sed egestas accumsan tellus id pulvinar. Mauris sit amet dignissim nuncpellentesque quis maximus velitsuspendisse blandit<br>velit quis metus tristique varius.</p>
    </div>
    <div class="service" style="left:630px">
      <div class="icon"><span style="font-size:46px;font-weight:900;color:#444">$</span></div>
      <h4>INVESTMENT<br>STRATEGY</h4>
      <p>Sed egestas accumsan tellus id pulvinar. Mauris sit amet dignissim nuncpellentesque quis maximus velitsuspendisse blandit<br>velit quis metus tristique varius.</p>
    </div>
    <div class="btn" style="left:240px;top:367px;width:180px;height:49px">READ MORE</div>
    <div class="btn" style="left:780px;top:367px;width:180px;height:49px">READ MORE</div>
  </section>

  <section class="abs team">
    <svg width="1200" height="479" viewBox="0 0 1200 479" style="position:absolute;left:0;top:0">
      <polygon fill="var(--blue)" points="0,0 200,0 0,70"/>
      <polygon fill="var(--red)" points="200,0 380,0 0,215 0,70"/>
      <polygon fill="var(--red)" points="590,0 1200,0 1200,235"/>
      <polygon fill="var(--blue)" points="880,0 1200,0 1200,130"/>
    </svg>
    <h2 class="section-title" style="top:50px">OUR TEAM</h2>
    <div class="member" style="left:75px"><div class="photo" role="img" aria-label="Portrait of Grant L Ashby"></div><h5>GRANT L ASHBY</h5><span>Founder &amp; Fund Manager</span></div>
    <div class="member" style="left:344px"><div class="photo" role="img" aria-label="Portrait of Claire Whitford"></div><h5>CLAIRE WHITFORD</h5><span>Founder &amp; Managing Partner</span></div>
    <div class="member" style="left:613px"><div class="photo" role="img" aria-label="Portrait of Ray Dorsan"></div><h5>RAY DORSAN</h5><span>Fund Advisor</span></div>
    <div class="member" style="left:884px"><div class="photo" role="img" aria-label="Portrait of Neil Barrow"></div><h5>NEIL BARROW</h5><span>Chief Investment Officer</span></div>
  </section>

  <section class="abs banner" role="img" aria-label="Ski racer in a tuck position against a blue sky">
    <svg width="1200" height="369" viewBox="0 0 1200 369" style="position:absolute;left:0;top:0">
      <polygon fill="var(--red)" points="0,130 560,369 360,369 0,220"/>
      <polygon fill="var(--red)" points="1200,110 1200,200 700,369 480,369"/>
    </svg>
    <p>TOTALLY COMMITTED AND FOCUSED ON CAPITAL<br>PRESERVATION AND UNINTERRUPTED<br>INCOME FOR OUR INVESTORS</p>
  </section>

  <h2 class="section-title" style="top:2912px">BLOG</h2>
  <article class="post" style="left:75px">
    <div class="img" role="img" aria-label="Stacks of coins with a rising financial chart" style="background:linear-gradient(135deg,#7d9be0,#1f4ab0 50%,#0b1f5c)"></div>
    <h6>LOREM IPSUM DOLOR SIT AMET</h6>
    <p>Nam vehicula pharetra mi, a varius nisl rhoncus volutpat.nunc quis lobortis nisl. Donec sit amet tortor eu tellus ultricies tempus sed quis augue ellentesque quis maximus velit blandit velit qui</p>
    <div class="btn">READ MORE</div>
  </article>
  <article class="post" style="left:614px">
    <div class="img" role="img" aria-label="Business people reviewing charts on a tablet and papers" style="background:linear-gradient(135deg,#3b4a66,#c9d3de 55%,#8995a6)"></div>
    <h6>LOREM IPSUM DOLOR SIT AMET</h6>
    <p>Nam vehicula pharetra mi, a varius nisl rhoncus volutpat.nunc quis lobortis nisl. Donec sit amet tortor eu tellus ultricies tempus sed quis augue ellentesque quis maximus velit blandit velit qui</p>
    <div class="btn">READ MORE</div>
  </article>
  <div class="dots"><i></i><i></i><i></i></div>

  <footer class="abs footer">
    <svg width="1200" height="594" viewBox="0 0 1200 594" style="position:absolute;left:0;top:0">
      <polygon fill="var(--blue)" points="0,0 419,10 0,270"/>
      <polygon fill="var(--blue)" points="1200,0 1200,230 419,10"/>
      <polygon fill="var(--red)" points="0,270 419,10 1200,230 1200,430 520,190 0,460"/>
      <polygon role="img" aria-label="Silhouette of a climber on a dark mountain summit" fill="#2a2a2c" points="0,460 520,190 1200,430 1200,594 0,594"/>
    </svg>
  </footer>
  <div class="fbrand">VANTOR CAPITAL II<small>MANAGEMENT, LLC</small></div>
  <p class="copy">Copyright © 2019. Company Name.<br>All Right Reserved</p>
  <div class="fcol" style="left:343px">
    <h6>SITE MAP</h6>
    <div style="display:flex;gap:60px">
      <div><a href="#">Home</a><a href="#">About Us</a><a href="#">Servicies</a><a href="#">Our Team</a><a href="#">Blog</a></div>
      <div><a href="#">Clients</a><a href="#">Contact Us</a></div>
    </div>
  </div>
  <div class="fcol info" style="left:599px">
    <h6>CONTACT INFO</h6>
    <ul>
      <li><svg width="12" height="16" viewBox="0 0 12 16" fill="#ccc"><path d="M6 0a6 6 0 0 0-6 6c0 4.5 6 10 6 10s6-5.5 6-10a6 6 0 0 0-6-6zm0 8.5A2.5 2.5 0 1 1 6 3.5a2.5 2.5 0 0 1 0 5z"/></svg>412 Harlow Lane,<br>Kelton,<br>KT7 2QP</li>
      <li><svg width="13" height="13" viewBox="0 0 24 24" fill="#ccc"><path d="M6.6 10.8c1.4 2.8 3.8 5.1 6.6 6.6l2.2-2.2c.3-.3.7-.4 1-.2 1.1.4 2.3.6 3.6.6.6 0 1 .4 1 1V20c0 .6-.4 1-1 1C10.6 21 3 13.4 3 4c0-.6.4-1 1-1h3.5c.6 0 1 .4 1 1 0 1.3.2 2.5.6 3.6.1.3 0 .7-.2 1z"/></svg>1-800-555-0142</li>
      <li><svg width="14" height="11" viewBox="0 0 24 18" fill="#ccc"><path d="M0 0h24v2L12 10 0 2z M0 4l12 8 12-8v14H0z"/></svg>info@vantorcapital.com</li>
    </ul>
  </div>
  <div class="fcol" style="left:872px">
    <h6>EMAIL SIGN UP</h6>
    <div class="email-box">Enter Email</div>
  </div>
  <div class="signup">SIGN UP</div>
  <div class="social"><i></i><i></i><i></i><i></i><i></i></div>

</div>
</body>
</html>
```